Visitenkarten für Urologisches Zentrum
Zielgruppe
Urologisches Zentrum Lindenhof / Vasektomie-Zentrum Lindenhof
Aufgabenstellung
Bitte an der alten Vorlage orientieren. Die 1. Seite (Aussenseite der Klappkarte) ist in Ordnung.
2. Seite (Innenseite der Klappkarte): Hier ggf. eine besser lesbare Schrift.
Adresse: Dr. med. FELIX BRANDT &
Dr. med. MARTIN SOMMER
Eibenweg 7
68161 Mannheim
Fon: unverändert, jedoch bitte etwas übersichtlicher
Fax: unverändert, jedoch bitte etwas übersichtlicher
E-Mail: unverändert, jedoch bitte etwas übersichtlicher
Web: unverändert, jedoch bitte etwas übersichtlicher
Öffnungszeiten: Mo,Di: 08:00 - 12:00 Uhr
14:00 - 16:00 Uhr
Mi: 08:00 - 12:00 Uhr
Do,Fr: 08.00 - 12:00 Uhr
Es sollte noch folgender Text eingefügt werden: Wußten Sie schon? Sie können bei uns Termine über www.terminvorbei.de
vereinbaren.
Bitte machen Sie uns einige dynamischere Gestaltungsvorschläge. Die Karte sollte in weiß gehalten werden. Keine Glanzbeschichtung und etwas kräftigeres, hochwertiges Papier.
Ich freue mich auf Ihre Vorschläge.

```html
<!DOCTYPE html>
<html lang="de">
<head>
<meta charset="utf-8">
<title>Visitenkarte Urologisches Zentrum Lindenhof</title>
<link href="https://fonts.googleapis.com/css2?family=Mulish:wght@400;500;700;800&display=swap" rel="stylesheet">
<style>
:root{
  --stage:#333333;
  --card:#ffffff;
  --green:#86b536;
  --ink:#1a1a1a;
  --map:#e9ecef;
  --rule:#c9c9c9;
}
html,body{margin:0;padding:0;overflow:hidden;}
body{width:1200px;height:826px;background:var(--stage);position:relative;font-family:"Mulish",sans-serif;color:var(--ink);}
.card{position:absolute;left:136px;width:928px;height:306px;background:var(--card);border:1px solid var(--rule);box-sizing:border-box;}
.card--outside{top:79px;}
.card--inside{top:441px;}
.accent{position:absolute;background:var(--green);height:12px;}
.accent--top{right:0;top:0;width:232px;}
.accent--bottom{left:231px;bottom:0;width:232px;}
.map-area{position:absolute;left:0;top:0;width:458px;height:304px;background:linear-gradient(135deg,#eef0f2,#dfe3e7);}
.brand{position:absolute;left:560px;top:120px;width:300px;text-align:center;}
.brand__mark{width:14px;height:14px;border-radius:50%;background:var(--green);margin:0 auto 14px;}
.brand__name{font-weight:800;font-size:17px;letter-spacing:.5px;color:var(--ink);text-transform:uppercase;line-height:1.2;}
.practice{position:absolute;left:72px;top:36px;font-size:19px;line-height:24px;font-weight:500;}
.contact{position:absolute;left:72px;top:98px;font-size:12.5px;list-style:none;margin:0;padding:0;}
.contact li{position:relative;padding-left:27px;line-height:18.5px;margin-bottom:4px;}
.contact .icon{position:absolute;left:0;top:1px;width:17px;height:17px;}
.hours-title{position:absolute;left:498px;top:38px;font-size:18px;font-weight:500;}
.hours{position:absolute;left:589px;top:86px;width:212px;border-collapse:collapse;font-size:15px;}
.hours td{padding:2px 0 3px;border-bottom:1.5px solid var(--green);}
.hours tr:last-child td{border-bottom:none;}
.hours .day{color:var(--green);width:58px;}
.hours .sep{color:var(--green);width:38px;}
.hint{position:absolute;right:46px;top:215px;text-align:right;}
.hint__title{font-size:29px;color:var(--green);font-weight:500;line-height:34px;}
.hint__text{font-size:15px;line-height:18px;}
.hint__link{font-size:15px;color:var(--green);line-height:18px;}
</style>
</head>
<body>
<section class="card card--outside">
  <div class="map-area" role="img" aria-label="Stadtplan Mannheim mit Rhein, Neckar und Markierung des Praxisstandorts"></div>
  <div class="accent accent--top"></div>
  <div class="accent accent--bottom"></div>
  <div class="brand">
    <div class="brand__mark"></div>
    <div class="brand__name">Urologisches Zentrum Lindenhof</div>
  </div>
</section>

<section class="card card--inside">
  <div class="accent accent--top"></div>
  <div class="accent accent--bottom"></div>
  <div class="practice">Urologisches Zentrum Lindenhof (UZL)<br>Vasektomie-Zentrum Lindenhof</div>
  <ul class="contact">
    <li><svg class="icon" viewBox="0 0 20 20"><circle cx="10" cy="10" r="10" fill="var(--green)"/><path d="M10 4a4 4 0 0 0-4 4c0 3 4 8 4 8s4-5 4-8a4 4 0 0 0-4-4zm0 5.5a1.5 1.5 0 1 1 0-3 1.5 1.5 0 0 1 0 3z" fill="#fff"/></svg>Dr. med. FELIX BRANDT &amp; Dr. med. MARTIN SOMMER<br>Eibenweg 7<br>68161 Mannheim</li>
    <li><svg class="icon" viewBox="0 0 20 20"><circle cx="10" cy="10" r="10" fill="var(--green)"/><path d="M7 5l2 2-1 1.5c.7 1.5 2 2.8 3.5 3.5L13 11l2 2-1.5 1.5C10 14 6 10 5.5 6.5z" fill="#fff"/></svg>0621 387 41 | 0621 552 190 27</li>
    <li><svg class="icon" viewBox="0 0 20 20"><circle cx="10" cy="10" r="10" fill="var(--green)"/><rect x="7" y="5" width="6" height="3" fill="#fff"/><rect x="5" y="8.5" width="10" height="5" rx="1" fill="#fff"/><rect x="7" y="12" width="6" height="3" fill="#fff" stroke="var(--green)" stroke-width=".8"/></svg>0621 387 42</li>
    <li><svg class="icon" viewBox="0 0 20 20"><circle cx="10" cy="10" r="10" fill="var(--green)"/><rect x="5" y="6.5" width="10" height="7" fill="#fff"/><path d="M5 6.5l5 4 5-4" fill="none" stroke="var(--green)" stroke-width="1"/></svg>praxis@brandt-sommer.de</li>
    <li><svg class="icon" viewBox="0 0 20 20"><circle cx="10" cy="10" r="10" fill="var(--green)"/><g fill="none" stroke="#fff" stroke-width="1"><circle cx="10" cy="10" r="5"/><ellipse cx="10" cy="10" rx="2.2" ry="5"/><path d="M5 10h10"/></g></svg>www.brandt-sommer.de</li>
  </ul>
  <div class="hours-title">Öffnungszeiten:</div>
  <table class="hours">
    <tr><td class="day">Mo, Di</td><td class="sep">:</td><td>8.00 - 17.00 Uhr</td></tr>
    <tr><td class="day">Mi</td><td class="sep">:</td><td>8.00 - 12.00 Uhr</td></tr>
    <tr><td class="day">Do</td><td class="sep">:</td><td>8.00 - 17.00 Uhr</td></tr>
    <tr><td class="day">Fr</td><td class="sep">:</td><td>8.00 - 16.00 Uhr</td></tr>
  </table>
  <div class="hint">
    <div class="hint__title">Wußten Sie schon?</div>
    <div class="hint__text">Sie können bei uns Termine über :</div>
    <div class="hint__link">www.terminvorbei.de</div>
  </div>
</section>
</body>
</html>
```